Voranta Imports Busisness cards and logo

Voranta imports is a brand new wholesale company located in Londonderry, New Hampshire dedicated to finding unique products from around the world.
Licensed to sell wine and spirits in the state and also authorized distributors of Pale Meadow Design, a manufacturer of girls and women shoes. Other products that we are currently trying to import are cheese and frozen food from Spain.
We would like a design that portraits our diversity of products and wholesale capabilities

```html
<!DOCTYPE html>
<html lang="en">
<head>
<meta charset="utf-8">
<title>Voranta Imports — Business Card</title>
<link href="https://fonts.googleapis.com/css2?family=Exo+2:wght@400;600;700&family=Michroma&display=swap" rel="stylesheet">
<style>
  :root {
    --stage: #2b2b2b;
    --paper: #ffffff;
    --green-deep: #1d6b1f;
    --green-mid: #2f8f2a;
    --lime: #8cc63f;
    --lime-bright: #b5dc3a;
    --brand-green: #2a7d1e;
    --ink-light: #ffffff;
  }
  * { box-sizing: border-box; margin: 0; padding: 0; }
  html, body { width: 1200px; height: 944px; overflow: hidden; }
  body { background: var(--stage); position: relative; }

  .business-card {
    position: absolute; left: 380px; top: 92px;
    width: 440px; height: 760px;
    box-shadow: 0 20px 50px rgba(0,0,0,.45);
  }
  .card-shapes { position: absolute; inset: 0; }

  .brand {
    position: absolute; left: 0; right: 0; top: 70px;
    display: flex; flex-direction: column; align-items: center; gap: 22px;
  }
  .brand-dot {
    width: 96px; height: 96px; border-radius: 50%;
    background: var(--lime);
  }
  .brand-name {
    font-family: "Exo 2", sans-serif; font-weight: 700;
    font-size: 40px; color: var(--brand-green); letter-spacing: .5px;
  }

  .person {
    position: absolute; left: 52px; top: 378px; color: var(--ink-light);
  }
  .person-name {
    font-family: "Michroma", sans-serif; font-size: 30px; letter-spacing: 1px;
    text-transform: uppercase;
  }
  .person-role {
    font-family: "Michroma", sans-serif; font-size: 15px; letter-spacing: 2px;
    text-transform: uppercase; margin-top: 8px;
  }

  .contact-list {
    position: absolute; left: 52px; top: 500px; list-style: none;
    display: flex; flex-direction: column; gap: 14px;
  }
  .contact-item {
    display: flex; align-items: center; gap: 12px;
    font-family: "Michroma", sans-serif; font-size: 12px; color: var(--ink-light);
  }
  .contact-icon { width: 20px; height: 20px; flex: none; }
</style>
</head>
<body>
  <article class="business-card">
    <svg class="card-shapes" width="440" height="760" viewBox="0 0 440 760" aria-hidden="true">
      <defs>
        <radialGradient id="green-body" cx="50%" cy="45%" r="70%">
          <stop offset="0" stop-color="#3a9a33"/>
          <stop offset="1" stop-color="#155c18"/>
        </radialGradient>
      </defs>
      <rect width="440" height="760" fill="#ffffff"/>
      <polygon points="0,330 40,300 400,300 440,330 440,725 0,725" fill="url(#green-body)"/>
      <polygon points="0,330 40,300 40,725 0,725" fill="#8cc63f"/>
      <polygon points="400,300 440,330 440,725 400,725" fill="#8cc63f"/>
      <polygon points="22,315 40,302 40,725 22,725" fill="#b5dc3a"/>
      <polygon points="400,302 418,315 418,725 400,725" fill="#b5dc3a"/>
      <rect x="0" y="725" width="440" height="6" fill="#b5dc3a"/>
    </svg>

    <header class="brand">
      <span class="brand-dot"></span>
      <span class="brand-name">Voranta Imports</span>
    </header>

    <section class="person">
      <h1 class="person-name">Marcus Hale</h1>
      <p class="person-role">General Manager</p>
    </section>

    <ul class="contact-list">
      <li class="contact-item">
        <svg class="contact-icon" viewBox="0 0 20 20"><circle cx="10" cy="10" r="10" fill="#fff"/><path d="M7 5h2l1 3-1.5 1a6 6 0 0 0 2.5 2.5l1-1.5 3 1v2c0 .6-.4 1-1 1A8 8 0 0 1 6 6c0-.6.4-1 1-1z" fill="#1d6b1f"/></svg>
        014 555 0192
      </li>
      <li class="contact-item">
        <svg class="contact-icon" viewBox="0 0 20 20"><circle cx="10" cy="10" r="10" fill="#fff"/><rect x="5" y="6" width="10" height="9" rx="1" fill="#1d6b1f"/><rect x="7" y="4" width="6" height="3" fill="#1d6b1f"/></svg>
        014 555 0192
      </li>
      <li class="contact-item">
        <svg class="contact-icon" viewBox="0 0 20 20"><circle cx="10" cy="10" r="10" fill="#fff"/><rect x="5" y="6.5" width="10" height="7" fill="none" stroke="#1d6b1f" stroke-width="1.4"/><path d="M5 7l5 4 5-4" fill="none" stroke="#1d6b1f" stroke-width="1.4"/></svg>
        hello@vorantaimports.com
      </li>
      <li class="contact-item">
        <svg class="contact-icon" viewBox="0 0 20 20"><circle cx="10" cy="10" r="10" fill="#fff"/><circle cx="10" cy="10" r="5" fill="none" stroke="#1d6b1f" stroke-width="1.4"/><path d="M5 10h10M10 5c-2 3-2 7 0 10M10 5c2 3 2 7 0 10" fill="none" stroke="#1d6b1f" stroke-width="1"/></svg>
        www.vorantaimports.com
      </li>
      <li class="contact-item">
        <svg class="contact-icon" viewBox="0 0 20 20"><circle cx="10" cy="10" r="10" fill="#fff"/><path d="M10 4a4 4 0 0 0-4 4c0 3 4 8 4 8s4-5 4-8a4 4 0 0 0-4-4z" fill="#1d6b1f"/><circle cx="10" cy="8" r="1.5" fill="#fff"/></svg>
        27 Harbor Lane Londonderry NH
      </li>
    </ul>
  </article>
</body>
</html>
```